RW Holloway LLC Business Card - Civil Engineering & Consulting Firm

We need a Business Card that is elegant, and masculine.  It is our Professional Civil Engineering & Consulting Company located in San Antonio TX (Not s construction or builder firm- no gears & no tool images please). We provide civil engineering services including  commercial site plans, grading and drainage plans, utility plans, hydraulics and hydrology, land planning, utility coordination, and other general civil engineering services related to commercial and residential development.
We have 2 existing Logos. We would like to convey reliability, strength, trustworthiness and attention to detail.  Blues and orange tones as per logo We are OK with the use of a darker blue in the mix.  We have 2 logo versions - Full Company Name Logo to go on the back of card, & Small Icon Logo for the front w/ personal Info.

Target Market(s)
Architects, Real Estate Developers, Other Strctural Engineers, Surveyers, General Contractors
Industry/Entity Type
Professional Civil Engineering
Contact Information for Business Card
Name, Position, Address, Cell & Office #, email, and company website
Font styles to use
Other font styles liked:
- Avian
Requirements
Should not have
- No Tools, No Gears, no Cranes, or Construction Equipment.

```html
<!DOCTYPE html>
<html lang="en">
<head>
<meta charset="utf-8">
<title>RW Holloway LLC – Business Card</title>
<link rel="stylesheet" href="https://fonts.googleapis.com/css2?family=Montserrat:wght@400;500;700&display=swap">
<style>
  :root {
    --stage: #c9c9c9;
    --card-white: #ffffff;
    --orange: #ee8a25;
    --ink: #1e1e1e;
    --sky: #7ea9d1;
    --sand: #b7a590;
    --amber: #e9953c;
    --paper-white: #ffffff;
  }
  * { box-sizing: border-box; margin: 0; padding: 0; }
  html, body { width: 1200px; height: 813px; overflow: hidden; }
  body {
    background: var(--stage);
    font-family: "Montserrat", sans-serif;
    display: flex;
    align-items: center;
    justify-content: center;
    gap: 40px;
  }
  .card {
    position: relative;
    width: 540px;
    height: 309px;
    overflow: hidden;
    box-shadow: 0 6px 18px rgba(0,0,0,0.18);
  }

  /* Front */
  .card-front { background: var(--card-white); color: var(--ink); }
  .corner-tab {
    position: absolute; top: 0; right: 0;
    width: 44px; height: 30px; background: var(--orange);
  }
  .identity {
    position: absolute; top: 40px; right: 64px; text-align: right;
  }
  .person-name {
    color: var(--orange); font-weight: 700; font-size: 22px; letter-spacing: 0.5px;
  }
  .person-role { font-size: 15px; font-weight: 400; margin-top: 2px; }
  .divider {
    position: absolute; left: 132px; right: 44px; top: 148px;
    height: 1.5px; background: var(--orange);
  }
  .brand-mark {
    position: absolute; left: 28px; top: 112px;
    display: flex; align-items: center; gap: 6px;
    color: var(--orange); font-weight: 700; font-size: 15px;
  }
  .brand-mark .dot { width: 10px; height: 10px; background: var(--orange); }
  .contact-list {
    position: absolute; left: 132px; top: 168px; list-style: none;
    font-size: 14.5px; line-height: 25px;
  }
  .contact-list li { display: flex; align-items: center; gap: 10px; }
  .contact-list svg { width: 14px; height: 14px; flex: none; }
  .address {
    position: absolute; right: 40px; top: 186px; text-align: left;
    font-size: 14.5px; line-height: 22px;
  }

  /* Back */
  .card-back {
    background: linear-gradient(160deg, var(--sky) 0%, var(--sand) 50%, var(--amber) 100%);
    color: var(--paper-white);
    display: flex; flex-direction: column; align-items: center; justify-content: center;
  }
  .company-name {
    font-weight: 500; font-size: 38px; letter-spacing: 3px;
  }
  .tagline-row {
    display: flex; align-items: center; gap: 12px; margin-top: 14px; width: 420px;
  }
  .tagline-row .rule { flex: 1; height: 1.5px; background: var(--paper-white); }
  .tagline {
    font-size: 13px; letter-spacing: 6px; font-weight: 400; white-space: nowrap;
  }
</style>
</head>
<body>
  <section class="card card-front" aria-label="Business card front">
    <div class="corner-tab"></div>
    <div class="identity">
      <p class="person-name">DREW CALLOWAY</p>
      <p class="person-role">Co-Founder</p>
    </div>
    <div class="brand-mark"><span class="dot"></span>RW Holloway LLC</div>
    <div class="divider"></div>
    <ul class="contact-list">
      <li><svg viewBox="0 0 16 16"><path fill="#ee8a25" d="M3 1l3 3-1.5 2a9 9 0 0 0 5.5 5.5L12 10l3 3-2 2C7 15 1 9 1 3z"/></svg>555-210-0148</li>
      <li><svg viewBox="0 0 16 16"><rect x="2" y="3" width="12" height="11" rx="2" fill="#ee8a25"/><rect x="5" y="6" width="6" height="5" fill="#fff"/></svg>555-210-0392</li>
      <li><svg viewBox="0 0 16 16"><rect x="1" y="3" width="14" height="10" fill="#ee8a25"/><path d="M1 3l7 6 7-6" stroke="#fff" fill="none" stroke-width="1.3"/></svg>info@rwhollowayllc</li>
      <li><svg viewBox="0 0 16 16"><circle cx="8" cy="8" r="7" fill="#ee8a25"/><path d="M1 8h14M8 1c-3 4-3 10 0 14M8 1c3 4 3 10 0 14" stroke="#fff" fill="none" stroke-width="1"/></svg>www.hollowaycivil.com</li>
    </ul>
    <div class="address">
      <p>4170 N. Cedar Ridge Road</p>
      <p>Suite 210 Alamo.12</p>
    </div>
  </section>

  <section class="card card-back" aria-label="Business card back">
    <p class="company-name">RW HOLLOWAY LLC</p>
    <div class="tagline-row">
      <span class="rule"></span>
      <span class="tagline">CONSULTING ENGINEERS</span>
      <span class="rule"></span>
    </div>
  </section>
</body>
</html>
```